Business Cards for new orthopaedic surgery practice

My husband and I are starting our own orthopaedic surgery practice. We are looking for a business card that is uniform, but one will have my name/title and the other will have his. You can just create one design with my name on it for now. But when I choose your design as the winning design I will ask that you add another copy with his name/title.

We are looking for classy, simple, elite all in one. We like dark blues/a little gold/yellow. Something that goes with our logo. We want our logo incorporated. Here is all the info you need:
Business name: RV Bone & Vitality Center
Location: 38517 North Willowmere Ave
Coral Springs, FL 33071
Phone: 954-218-4063
Fax: 954-582-7341
Email: info@myrvbonecare.example

Names: Lydia Vance, M.D.
Board Certified Hand and Upper Extremity Surgeon

Ebo Dansu, M.D.
Board Certified Hip & Knee Replacement/General Orthopaedic Surgeon

Can decide what you want to put on the back. Maybe a slogan:
Rooted in Care. Focused on You

I am just going to upload our logo. The only thing is if we select you as the winning design, the location, and phone numbers may change. We will need your help to update that once fully solidified.

Industry/Entity Type

Medical

Contact Information for Business Card

Colors
0054AA
0677BA
7BADD7
CADEEF
E8F1F8
0094D4
00A9DD
6FCCEA
C7EBF8
E9F6FB

Requirements
Must have
• class, appeal,
Should not have
• We want to air on the side of masculine if we are looking at masculine vs. feminine feel. But we still want it classy, sophisticated, and something we will love

```html
<!DOCTYPE html>
<html lang="en">
<head>
<meta charset="utf-8">
<title>RV Bone &amp; Vitality Center – Business Card</title>
<link rel="stylesheet" href="https://fonts.googleapis.com/css2?family=Poppins:wght@400;600&display=swap">
<style>
  :root{
    --stage:#1c1c1f;
    --navy:#283c86;
    --navy-deep:#223475;
    --pattern:#3550a6;
    --cyan:#1bbde2;
    --white:#ffffff;
  }
  *{box-sizing:border-box;margin:0;padding:0}
  html,body{width:1200px;height:900px;overflow:hidden;background:var(--stage);font-family:"Poppins",sans-serif}
  .canvas{position:relative;width:1200px;height:900px}
  .card{position:absolute;left:250px;width:700px;height:400px;background:var(--navy);overflow:hidden;box-shadow:0 12px 30px rgba(0,0,0,.5)}
  .card--front{top:35px}
  .card--back{top:465px}
  .swoosh{position:absolute;inset:0;width:100%;height:100%}
  .brand{position:absolute;left:58px;top:92px;display:flex;align-items:center;gap:12px}
  .brand__dot{width:14px;height:14px;border-radius:50%;background:var(--white)}
  .brand__name{color:var(--white);font-weight:600;font-size:22px;letter-spacing:.5px;line-height:1.25;width:230px}
  .divider{position:absolute;left:372px;top:120px;width:1px;height:170px;background:var(--cyan)}
  .contact{position:absolute;left:392px;top:118px;color:var(--white);font-size:14.5px;line-height:1.45}
  .contact__name{color:var(--cyan);font-weight:600;font-size:20px;line-height:1.3}
  .contact__title{margin-bottom:10px}
  .contact__row{display:flex;align-items:center;gap:7px}
  .contact__row svg{width:13px;height:13px;fill:var(--white);flex:none}
  .contact__address{margin-bottom:10px}
  .pattern{position:absolute;inset:0;background:linear-gradient(135deg,var(--pattern),var(--navy-deep) 55%,var(--pattern))}
  .back-brand{position:absolute;left:50%;top:50%;transform:translate(-50%,-50%);display:flex;align-items:center;gap:14px}
  .back-brand .brand__name{width:auto;font-size:26px;white-space:nowrap}
</style>
</head>
<body>
<div class="canvas">
  <section class="card card--front">
    <svg class="swoosh" viewBox="0 0 700 400" aria-hidden="true">
      <path d="M0,250 C70,300 200,320 360,340 C500,356 600,370 640,400 L0,400 Z" fill="var(--cyan)"/>
      <path d="M0,150 C10,230 120,285 470,350 C170,300 40,262 30,160 Z" fill="var(--white)"/>
    </svg>
    <div class="brand">
      <span class="brand__dot"></span>
      <span class="brand__name">RV Bone &amp; Vitality Center</span>
    </div>
    <div class="divider"></div>
    <div class="contact">
      <p class="contact__name">Lydia Vance, M.D.</p>
      <p class="contact__title">Hand and Upper Extremity Surgery</p>
      <p class="contact__address">38517 North Willowmere Ave<br>Coral Springs, FL 33071</p>
      <p class="contact__row"><svg viewBox="0 0 24 24"><path d="M6.6 10.8a15.1 15.1 0 0 0 6.6 6.6l2.2-2.2a1 1 0 0 1 1-.25 11.4 11.4 0 0 0 3.6.57 1 1 0 0 1 1 1V20a1 1 0 0 1-1 1A17 17 0 0 1 3 4a1 1 0 0 1 1-1h3.5a1 1 0 0 1 1 1c0 1.25.2 2.45.57 3.57a1 1 0 0 1-.25 1z"/></svg>954-218-4063</p>
      <p class="contact__row"><svg viewBox="0 0 24 24"><path d="M6 3h10v5H6zM4 9h16a2 2 0 0 1 2 2v6h-4v4H6v-4H2v-6a2 2 0 0 1 2-2zm4 7v3h8v-3z"/></svg>954-582-7341</p>
      <p class="contact__row"><svg viewBox="0 0 24 24"><path d="M3 5h18v14H3zm2 2v.5l7 5 7-5V7l-7 5z"/></svg>info@myrvbonecare.example</p>
    </div>
  </section>

  <section class="card card--back">
    <div class="pattern" role="img" aria-label="Repeating tone-on-tone pattern of the practice emblem"></div>
    <div class="back-brand">
      <span class="brand__dot"></span>
      <span class="brand__name">RV Bone &amp; Vitality Center</span>
    </div>
  </section>
</div>
</body>
</html>
```